Broschüren-Design für gemeinnützige Organisation
moonsparrows suchte ein neues Design in der Kategorie Broschüre und hat ein Projekt auf gestaltwerkstatt.de gestartet.
Zielgruppe
Als gemeinnützige Organisation unterstützen wir Kinder und Jugendliche, vor allem in den Bereichen Schul- und Berufsausbildung. Wir arbeiten vorwiegend in Ostafrika, vor allem in Tansania und Kenia. Mit dieser Broschüre wollen wir für unser neues Pilotprojekt werben, den Aufbau eines dualen Ausbildungszentrums für junge Menschen in Kenia. Ziel des Ausbildungszentrums ist es jungen Menschen eine qualifizierte Berufsausbildung zu ermöglichen und damit Perspektiven und Zukunft im Heimatland.
Unsere Zielgruppe: Menschen mit Herz und Weitblick von 18 bis 80+
Aufgabenstellung
Die Broschüre sollte handlich sein und leicht zum einstecken. Derzeit haben wir den Text und die Gestaltung auf das Format DIN lang hoch (105x210 mm, 12 Seiten) ausgelegt. Ist aber nur ein Vorschlag und kein muss.
Die einzige Vorgabe ist das orange aus dem Logo mit der Farbe #ff3300 Ansonsten gibt es keine Vorgaben was Schrift, Farbgestaltung, Layout, Form, Seitenanzahl...ect betrifft. Allerdings sollte darauf geachtet werden, dass die Textinhalte der Doppelseiten erhalten bleiben (z.B. Seite 2 links - Seite 3 rechts, usw.)
Mitgeliefert werden Fotos, die gerne Verwendung finden können. Sollten aber weitere oder aussagekräftigere Fotos und Hintergründe benötigt werden, sind wir absolut offen dafür.

```html
<!DOCTYPE html>
<html lang="de">
<head>
<meta charset="utf-8">
<title>Moonsparrows – Broschürenvarianten</title>
<link rel="stylesheet" href="https://fonts.googleapis.com/css2?family=Roboto+Condensed:wght@400;700&family=Roboto:wght@400;700&display=swap">
<style>
:root{
  --orange:#ef5a0f;
  --orange-dark:#d9480a;
  --navy:#262a5e;
  --text:#3a3a3a;
  --grey-body:#ececec;
  --stripe:#444;
  --label:#9a9a9a;
}
*{margin:0;padding:0;box-sizing:border-box}
html,body{width:1200px;height:5212px;overflow:hidden;background:#fff}
body{position:relative;font-family:"Roboto",sans-serif;color:var(--text)}
.panel{position:absolute;width:434px;height:870px;overflow:hidden;background:#fff;box-shadow:0 6px 22px rgba(0,0,0,.22)}
.panel.left{left:112px}
.panel.right{left:630px}
.panel svg.bg{position:absolute;left:0;top:0;width:434px;height:870px}
.variant-label{position:absolute;left:132px;font:700 36px "Roboto Condensed",sans-serif;color:var(--label)}
.tab{position:absolute;top:0;left:106px;width:224px;height:52px;background:var(--orange);color:#fff;font:700 19px/52px "Roboto Condensed",sans-serif;text-align:center;letter-spacing:.5px}
.title{position:absolute;left:34px;font:700 35px "Roboto Condensed",sans-serif;color:var(--orange);letter-spacing:.3px;white-space:nowrap}
.subtitle{position:absolute;left:34px;font:400 22px/29px "Roboto",sans-serif;color:var(--text);white-space:nowrap}
.on-orange{color:#fff}
.centered{left:0;width:434px;text-align:center}
.brand{position:absolute;display:flex;align-items:center;gap:8px}
.brand-mark{width:30px;height:30px;border-radius:50%;background:var(--orange);flex:none}
.brand-name{font:700 16px/15px "Roboto Condensed",sans-serif;color:var(--navy);text-transform:uppercase;white-space:nowrap}
.web-btn{position:absolute;height:26px;padding:0 16px;border-radius:5px;background:var(--orange);color:#fff;font:700 12px/26px "Roboto",sans-serif;white-space:nowrap}
.address{position:absolute;left:40px;font:400 12.5px/21px "Roboto",sans-serif;color:var(--text);white-space:nowrap}
.address span{display:inline-block;width:52px}
.donation{position:absolute;left:0;width:434px;text-align:center;font:400 12.5px/21px "Roboto",sans-serif;color:var(--text)}
.donation b{font-weight:700}
.donation.light{color:#ffd6c0}
.donation.light b{color:#fff}
.card{position:absolute;background:#fff;border-radius:8px 8px 0 0}
</style>
</head>
<body>

<svg width="0" height="0" style="position:absolute">
  <defs>
    <linearGradient id="photoChef" x1="0" y1="0" x2="1" y2="1">
      <stop offset="0" stop-color="#9b9893"/><stop offset=".55" stop-color="#6e6760"/><stop offset="1" stop-color="#d9d6d2"/>
    </linearGradient>
    <linearGradient id="photoGirls" x1="0" y1="0" x2="1" y2="1">
      <stop offset="0" stop-color="#5a4636"/><stop offset=".5" stop-color="#3b2a22"/><stop offset="1" stop-color="#3f8fb8"/>
    </linearGradient>
    <linearGradient id="bandGrad" x1="0" y1="0" x2="1" y2="1">
      <stop offset="0" stop-color="#f26a1f"/><stop offset="1" stop-color="#e0500c"/>
    </linearGradient>
  </defs>
</svg>

<!-- Variant A -->
<section class="panel left" style="top:116px">
  <svg class="bg" viewBox="0 0 434 870">
    <polygon role="img" aria-label="Foto: lächelnde junge Köchin in weißer Kochjacke in einer Großküche" points="0,0 434,0 434,470 0,520" fill="url(#photoChef)"/>
    <polygon points="0,520 434,470 434,486 0,540" fill="var(--orange)"/>
  </svg>
  <div class="title" style="top:564px">HEIMAT ALS CHANCE</div>
  <div class="subtitle" style="top:612px">Berufsausbildung benachteiligter<br>Jugendlicher in ihrer Heimat</div>
  <div class="brand" style="left:34px;top:720px"><span class="brand-mark"></span><span class="brand-name">Moonsparrows<br>Kinderhilfswerk e.V.</span></div>
  <div class="web-btn" style="left:34px;top:814px">www.moonsparrows.de</div>
</section>
<section class="panel right" style="top:116px">
  <svg class="bg" viewBox="0 0 434 870">
    <polygon role="img" aria-label="Foto: zwei lachende Mädchen mit Kopftüchern und Halsketten" points="0,0 434,0 434,440 0,505" fill="url(#photoGirls)"/>
    <polygon points="0,505 434,440 434,470 0,520" fill="var(--stripe)"/>
  </svg>
  <div class="tab">HERZLICHEN DANK</div>
  <div class="brand" style="left:40px;top:530px"><span class="brand-mark"></span><span class="brand-name">Moonsparrows<br>Kinderhilfswerk e.V.</span></div>
  <div class="address" style="top:620px">Lindenweg 47<br>98765 Nordfeld<br><span>Telefon:</span>0123 456 78 90<br><span>Email:</span>info@moonsparrows.de</div>
  <div class="web-btn" style="left:128px;top:732px">www.moonsparrows.de</div>
  <div class="donation" style="top:776px"><b>Spendenkonto</b><br>Stadtbank Nordfeld<br>IBAN: DE00 1234 5678 0000 1111 22</div>
</section>
<div class="variant-label" style="top:1008px">A</div>

<!-- Variant B -->
<section class="panel left" style="top:1120px;background:var(--grey-body)">
  <svg class="bg" viewBox="0 0 434 870">
    <polygon role="img" aria-label="Foto: lächelnde junge Köchin in weißer Kochjacke in einer Großküche" points="0,0 434,0 434,470 0,512" fill="url(#photoChef)"/>
    <polygon points="0,512 434,470 434,480 0,526" fill="var(--orange)"/>
  </svg>
  <div class="title" style="top:556px">HEIMAT ALS CHANCE</div>
  <div class="subtitle" style="top:604px">Berufsausbildung benachteiligter<br>Jugendlicher in ihrer Heimat</div>
  <div class="brand" style="left:34px;top:718px"><span class="brand-mark"></span><span class="brand-name">Moonsparrows<br>Kinderhilfswerk e.V.</span></div>
  <div class="web-btn" style="left:34px;top:812px">www.moonsparrows.de</div>
</section>
<section class="panel right" style="top:1120px;background:var(--grey-body)">
  <svg class="bg" viewBox="0 0 434 870">
    <polygon role="img" aria-label="Foto: zwei lachende Mädchen mit Kopftüchern und Halsketten" points="0,0 434,0 434,440 0,505" fill="url(#photoGirls)"/>
    <polygon points="0,505 434,440 434,470 0,520" fill="var(--stripe)"/>
  </svg>
  <div class="tab">HERZLICHEN DANK</div>
  <div class="brand" style="left:40px;top:530px"><span class="brand-mark"></span><span class="brand-name">Moonsparrows<br>Kinderhilfswerk e.V.</span></div>
  <div class="address" style="top:620px">Lindenweg 47<br>98765 Nordfeld<br><span>Telefon:</span>0123 456 78 90<br><span>Email:</span>info@moonsparrows.de</div>
  <div class="web-btn" style="left:128px;top:732px">www.moonsparrows.de</div>
  <div class="donation" style="top:776px"><b>Spendenkonto</b><br>Stadtbank Nordfeld<br>IBAN: DE00 1234 5678 0000 1111 22</div>
</section>
<div class="variant-label" style="top:2012px">B</div>

<!-- Variant C -->
<section class="panel left" style="top:2110px;background:var(--orange)">
  <svg class="bg" viewBox="0 0 434 870">
    <polygon points="0,0 434,0 434,500 0,548" fill="#fff"/>
    <polygon role="img" aria-label="Foto: lächelnde junge Köchin in weißer Kochjacke in einer Großküche" points="0,0 434,0 434,490 0,536" fill="url(#photoChef)"/>
  </svg>
  <div class="title on-orange centered" style="top:568px">HEIMAT ALS CHANCE</div>
  <div class="subtitle on-orange centered" style="top:616px">Berufsausbildung benachteiligter<br>Jugendlicher in ihrer Heimat</div>
  <div class="card" style="left:102px;top:704px;width:238px;height:166px"></div>
  <div class="brand" style="left:128px;top:718px"><span class="brand-mark"></span><span class="brand-name">Moonsparrows<br>Kinderhilfswerk e.V.</span></div>
  <div class="web-btn" style="left:128px;top:798px">www.moonsparrows.de</div>
</section>
<section class="panel right" style="top:2110px;background:var(--orange)">
  <svg class="bg" viewBox="0 0 434 870">
    <polygon points="0,0 434,0 434,490 0,530" fill="#fff"/>
    <polygon role="img" aria-label="Foto: zwei lachende Mädchen mit Kopftüchern und Halsketten" points="0,0 434,0 434,480 0,518" fill="url(#photoGirls)"/>
  </svg>
  <div class="tab">HERZLICHEN DANK</div>
  <div class="donation light" style="top:542px"><b>Spendenkonto</b><br>Stadtbank Nordfeld<br>IBAN: DE00 1234 5678 0000 1111 22</div>
  <div class="card" style="left:100px;top:618px;width:240px;height:252px"></div>
  <div class="brand" style="left:130px;top:636px"><span class="brand-mark"></span><span class="brand-name">Moonsparrows<br>Kinderhilfswerk e.V.</span></div>
  <div class="web-btn" style="left:130px;top:700px">www.moonsparrows.de</div>
  <div class="address" style="left:130px;top:744px">Lindenweg 47<br>98765 Nordfeld<br><span>Telefon:</span>0123 456 78 90<br><span>Email:</span>info@moonsparrows.de</div>
</section>
<div class="variant-label" style="top:3000px">C</div>

<!-- Variant D -->
<section class="panel left" style="top:3114px">
  <svg class="bg" viewBox="0 0 434 870">
    <rect role="img" aria-label="Foto: lächelnde junge Köchin in weißer Kochjacke in einer Großküche" x="0" y="0" width="434" height="460" fill="url(#photoChef)"/>
    <rect role="img" aria-label="Band mit grafischem Ethno-Muster in Grau" x="0" y="446" width="434" height="52" fill="#b9b7b3"/>
  </svg>
  <div class="title" style="top:544px">HEIMAT ALS CHANCE</div>
  <div class="subtitle" style="top:592px">Berufsausbildung benachteiligter<br>Jugendlicher in ihrer Heimat</div>
  <div class="brand" style="left:34px;top:690px"><span class="brand-mark"></span><span class="brand-name">Moonsparrows<br>Kinderhilfswerk e.V.</span></div>
  <div class="web-btn" style="left:34px;top:780px">www.moonsparrows.de</div>
</section>
<section class="panel right" style="top:3114px">
  <svg class="bg" viewBox="0 0 434 870">
    <rect role="img" aria-label="Foto: zwei lachende Mädchen mit Kopftüchern und Halsketten" x="0" y="0" width="434" height="450" fill="url(#photoGirls)"/>
    <rect role="img" aria-label="Band mit grafischem Ethno-Muster in Grau" x="0" y="436" width="434" height="52" fill="#b9b7b3"/>
  </svg>
  <div class="tab">HERZLICHEN DANK</div>
  <div class="brand" style="left:40px;top:544px"><span class="brand-mark"></span><span class="brand-name">Moonsparrows<br>Kinderhilfswerk e.V.</span></div>
  <div class="address" style="top:630px">Lindenweg 47<br>98765 Nordfeld<br><span>Telefon:</span>0123 456 78 90<br><span>Email:</span>info@moonsparrows.de</div>
  <div class="web-btn" style="left:128px;top:740px">www.moonsparrows.de</div>
  <div class="donation" style="top:782px"><b>Spendenkonto</b><br>Stadtbank Nordfeld<br>IBAN: DE00 1234 5678 0000 1111 22</div>
</section>
<div class="variant-label" style="top:4016px">D</div>

<!-- Variant E -->
<section class="panel left" style="top:4118px">
  <svg class="bg" viewBox="0 0 434 870">
    <polygon role="img" aria-label="Foto: lächelnde junge Köchin in weißer Kochjacke in einer Großküche" points="0,0 434,0 434,490 0,525" fill="url(#photoChef)"/>
    <polygon points="0,520 434,484 434,700 0,680" fill="url(#bandGrad)"/>
    <polygon points="0,680 434,700 434,712 0,688" fill="var(--orange-dark)"/>
  </svg>
  <div class="title on-orange" style="top:562px">HEIMAT ALS CHANCE</div>
  <div class="subtitle on-orange" style="top:604px">Berufsausbildung benachteiligter<br>Jugendlicher in ihrer Heimat</div>
  <div class="brand" style="left:34px;top:742px"><span class="brand-mark"></span><span class="brand-name">Moonsparrows<br>Kinderhilfswerk e.V.</span></div>
  <div class="web-btn" style="left:34px;top:818px">www.moonsparrows.de</div>
</section>
<section class="panel right" style="top:4118px">
  <svg class="bg" viewBox="0 0 434 870">
    <polygon role="img" aria-label="Foto: zwei lachende Mädchen mit Kopftüchern und Halsketten" points="0,0 434,0 434,470 0,505" fill="url(#photoGirls)"/>
  </svg>
  <div class="tab">HERZLICHEN DANK</div>
  <div class="brand" style="left:40px;top:540px"><span class="brand-mark"></span><span class="brand-name">Moonsparrows<br>Kinderhilfswerk e.V.</span></div>
  <div class="address" style="top:628px">Lindenweg 47<br>98765 Nordfeld<br><span>Telefon:</span>0123 456 78 90<br><span>Email:</span>info@moonsparrows.de</div>
  <div class="web-btn" style="left:128px;top:740px">www.moonsparrows.de</div>
  <div class="donation" style="top:784px"><b>Spendenkonto</b><br>Stadtbank Nordfeld<br>IBAN: DE00 1234 5678 0000 1111 22</div>
</section>
<div class="variant-label" style="top:5026px">E</div>

</body>
</html>
```